Woman owned consulting company needs an elegant and modern business card design

I need a business card design for my new consulting company, Mara Quillon Consulting. I am looking for something that is simple and elegant, but also creative and original. You can use either version of the logo that are attached. I have also included the information that needs to be featured on the business card.

Contact Information for Business Card

Requirements
Must have
• The logo and the font type and a standard business card size. Use shades of gray/silver and or rose gold that are in the logo.
• I didn't realize that my actual logo wasn't attached. Please incorporate in the designs.
Should not have
• Colors that are different from my logo

```html
<!DOCTYPE html>
<html lang="en">
<head>
<meta charset="utf-8">
<title>Mara Quillon Consulting — Business Card</title>
<link href="https://fonts.googleapis.com/css2?family=Cinzel:wght@400;600&family=Lora:wght@400;500&display=swap" rel="stylesheet">
<style>
  :root {
    --backdrop: #3a3a3c;
    --card: #232325;
    --silver: #c9c9cb;
    --silver-soft: #a9a9ad;
    --text-light: #e6e6e8;
    --band-light: #b8b8bb;
    --band-dark: #44484b;
  }
  * { margin: 0; padding: 0; box-sizing: border-box; }
  html, body {
    width: 799px; height: 1200px; overflow: hidden;
    background: var(--backdrop);
  }
  .canvas { position: relative; width: 799px; height: 1200px; }
  .card {
    position: absolute; left: 90px; width: 620px; height: 354px;
    background: var(--card);
    border-radius: 4px;
    box-shadow: 0 10px 28px rgba(0,0,0,0.45);
    overflow: hidden;
  }
  .card--front { top: 90px; }
  .card--back { top: 700px; }

  .front-name {
    position: absolute; inset: 0;
    display: flex; align-items: center; justify-content: center;
    text-align: center;
    font-family: 'Lora', serif; font-weight: 400;
    font-size: 46px; line-height: 1.15; color: var(--silver);
    padding: 0 70px;
  }

  .back-name {
    position: absolute; left: 40px; top: 72px; width: 230px;
    font-family: 'Lora', serif; font-weight: 400;
    font-size: 34px; line-height: 1.12; color: var(--silver);
  }

  .contact { position: absolute; left: 300px; top: 88px; }
  .contact__name {
    font-family: 'Cinzel', serif; font-weight: 600;
    font-size: 23px; letter-spacing: 1.5px; color: var(--text-light);
  }
  .contact__role {
    font-family: 'Lora', serif; font-size: 13px; color: var(--silver-soft);
    margin-top: -2px;
  }
  .contact__list { list-style: none; margin-top: 18px; }
  .contact__item {
    display: flex; align-items: center; gap: 8px;
    font-family: 'Lora', serif; font-size: 15px; color: var(--text-light);
    line-height: 21px;
  }
  .contact__item svg { width: 12px; height: 12px; flex: none; fill: var(--silver); }

  .bottom-band { position: absolute; left: 0; bottom: 0; width: 620px; height: 70px; }
  .company-line {
    position: absolute; left: 240px; right: 0; bottom: 0; height: 48px;
    display: flex; align-items: center; justify-content: center;
    font-family: 'Cinzel', serif; font-size: 17px; letter-spacing: 1px;
    color: var(--text-light); white-space: nowrap;
  }
</style>
</head>
<body>
<main class="canvas">

  <section class="card card--front" aria-label="Card front">
    <div class="front-name">Mara Quillon Consulting</div>
  </section>

  <section class="card card--back" aria-label="Card back">
    <div class="back-name">Mara Quillon Consulting</div>

    <div class="contact">
      <p class="contact__name">MARA QUILLON</p>
      <p class="contact__role">Owner</p>
      <ul class="contact__list">
        <li class="contact__item">
          <svg viewBox="0 0 24 24"><path d="M6.6 10.8a15 15 0 0 0 6.6 6.6l2.2-2.2c.3-.3.7-.4 1-.2 1.1.4 2.3.6 3.6.6.6 0 1 .4 1 1V20c0 .6-.4 1-1 1A17 17 0 0 1 3 4c0-.6.4-1 1-1h3.5c.6 0 1 .4 1 1 0 1.3.2 2.5.6 3.6.1.3 0 .7-.2 1z"/></svg>
          610-555-0142
        </li>
        <li class="contact__item">
          <svg viewBox="0 0 24 24"><path d="M2 5h20v14H2z M3.5 6.5 12 13l8.5-6.5" fill="none" stroke="#c9c9cb" stroke-width="2"/></svg>
          mara@maraquillonconsulting.com
        </li>
        <li class="contact__item">
          <svg viewBox="0 0 24 24"><circle cx="12" cy="12" r="9" fill="none" stroke="#c9c9cb" stroke-width="2"/><path d="M3 12h18M12 3c3 3 3 15 0 18M12 3c-3 3-3 15 0 18" fill="none" stroke="#c9c9cb" stroke-width="1.6"/></svg>
          www.maraquillonconsulting.com
        </li>
      </ul>
    </div>

    <svg class="bottom-band" viewBox="0 0 620 70" aria-hidden="true">
      <rect x="0" y="22" width="260" height="10" fill="var(--band-light)"/>
      <path d="M240 70 V38 Q240 22 256 22 H620 V70 Z" fill="var(--band-dark)"/>
    </svg>
    <p class="company-line">Mara Quillon Consulting, LLC</p>
  </section>

</main>
</body>
</html>
```